Business Card and Letterhead for Pimlu - modern real estate business

I need a double sided business card design for Pimlu. Please see business card brief here https://files.trelvonadocs.com/sheet/r/7QzTmWbaXLJnoPEd-kRyUgFhHsstbvCe2qfoMxDa_pz/view?mode=shared

Please feel free to design the business cards however you feel best. I am happy to give some creative freedoms and then provide feedback from there.

Please then also create a letterhead to match the business card design

Colors

Designer to choose colors to be used in the design.

Requirements
Must have
• Must be a modern, elegant business card which looks very professional

```html
<!DOCTYPE html>
<html lang="en">
<head>
<meta charset="UTF-8">
<title>Pimlu Business Card</title>
<link href="https://fonts.googleapis.com/css2?family=Montserrat:wght@500;600;800&display=swap" rel="stylesheet">
<style>
  :root {
    --brand-red: #e31e24;
    --card-black: #1f1d1d;
    --ink: #222222;
    --paper: #ffffff;
    --backdrop: #d9dadc;
    --photo-light: #f2f2f2;
    --photo-dark: #3a3a3e;
  }
  * { margin: 0; padding: 0; box-sizing: border-box; }
  html, body { width: 1200px; height: 800px; overflow: hidden; }
  body {
    background: var(--backdrop);
    font-family: "Montserrat", Arial, sans-serif;
    display: flex;
    flex-direction: column;
    align-items: center;
    justify-content: center;
    gap: 40px;
  }
  .card {
    width: 525px;
    height: 300px;
    position: relative;
    overflow: hidden;
    box-shadow: 0 4px 14px rgba(0,0,0,0.18);
  }
  .card-back {
    background: var(--card-black);
    display: flex;
    align-items: center;
    justify-content: center;
  }
  .wordmark {
    color: var(--brand-red);
    font-weight: 800;
    letter-spacing: 0.04em;
    text-transform: uppercase;
    line-height: 1;
  }
  .card-back .wordmark { font-size: 72px; }
  .card-front { background: var(--paper); }
  .card-front .wordmark {
    position: absolute;
    left: 38px;
    top: 30px;
    font-size: 38px;
  }
  .agent-details {
    position: absolute;
    left: 38px;
    top: 104px;
    color: var(--ink);
    font-size: 12px;
    font-weight: 500;
    line-height: 1.45;
  }
  .agent-name {
    color: var(--brand-red);
    font-weight: 600;
    font-size: 14px;
    letter-spacing: 0.02em;
    text-transform: uppercase;
  }
  .agent-title { margin-bottom: 14px; }
  .postal-address { margin-bottom: 12px; }
  .contact-list { list-style: none; }
  .contact-list li { display: flex; align-items: center; gap: 7px; }
  .contact-list svg { width: 11px; height: 11px; flex: none; }
  .bottom-rule {
    position: absolute;
    left: 0;
    bottom: 0;
    display: flex;
    gap: 5px;
    height: 11px;
  }
  .bottom-rule .accent { width: 40px; background: var(--brand-red); }
  .bottom-rule .band { width: 190px; background: var(--card-black); }
  .agent-photo {
    position: absolute;
    right: 20px;
    top: 60px;
    width: 270px;
    height: 240px;
    background: linear-gradient(180deg, var(--photo-light) 0%, #cfcfd1 35%, var(--photo-dark) 70%, #2a2a2d 100%);
  }
</style>
</head>
<body>
  <section class="card card-back">
    <div class="wordmark">Pimlu</div>
  </section>

  <section class="card card-front">
    <div class="wordmark">Pimlu</div>
    <div class="agent-details">
      <div class="agent-name">Liam Fairley</div>
      <div class="agent-title">Licenced Real Estate Agent</div>
      <div class="postal-address">PO Box 3174<br>Larchmere NSW 2791</div>
      <ul class="contact-list">
        <li>
          <svg viewBox="0 0 24 24"><path fill="#e31e24" d="M6.6 10.8a15.1 15.1 0 0 0 6.6 6.6l2.2-2.2c.3-.3.7-.4 1-.2 1.1.4 2.3.6 3.6.6.6 0 1 .4 1 1V20c0 .6-.4 1-1 1A17 17 0 0 1 3 4c0-.6.4-1 1-1h3.5c.6 0 1 .4 1 1 0 1.3.2 2.5.6 3.6.1.3 0 .7-.2 1z"/></svg>
          0400 555 218
        </li>
        <li>
          <svg viewBox="0 0 24 24"><rect x="2" y="5" width="20" height="14" fill="none" stroke="#e31e24" stroke-width="2.4"/><path d="M2 5l10 8 10-8" fill="none" stroke="#e31e24" stroke-width="2.4"/></svg>
          liam@pimlu.com
        </li>
        <li>
          <svg viewBox="0 0 24 24"><circle cx="12" cy="12" r="10" fill="none" stroke="#e31e24" stroke-width="2.2"/><ellipse cx="12" cy="12" rx="4.5" ry="10" fill="none" stroke="#e31e24" stroke-width="2"/><path d="M2 12h20" stroke="#e31e24" stroke-width="2"/></svg>
          www.pimlu.com
        </li>
      </ul>
    </div>
    <div class="bottom-rule"><span class="accent"></span><span class="band"></span></div>
    <div class="agent-photo" role="img" aria-label="Portrait photo of the agent in a dark suit and shirt"></div>
  </section>
</body>
</html>
```